Systems and Technology Consultants - Website

Design & Build a website for a new company which operates in the Systems and Technology space for Transportation, Government and Commercial sectors.

Overall design should be minimalist in nature.
Should also have a feed that provides news and event updates on the main page.
Logo has already been awarded and should be incorporated into the site.

We like the overall layout, functionality and simplicity of the below sites. Submitted designs could be similar to or a combination of the aspects on these sites, or perhaps a whole different concept - we are open to new ideas.
Norvique.com
Teblo.it

Update 1 Dated 27 May 2014

All I am moving away from the Teblo.it website and would like it to be more aligned with Norvique.com not only in layout but in functionality. I will be extending the deadline of this design brief for two weeks to incorporate additional requirements and will add addtional funding to the project.

Apologies for not having more information available to provide but with so many submissions its getting confusing.

Thanks Derek

Please note that the brief has been updated and the deadline has been extended.

Important: We will need two language versions of the website, English and Arabic; the website is hosted on HostPelican

Hello All, Thank you for your submissions. We have narrowed it down to the final 6 designers and I just wanted to take a moment and provide a bit of feedback regarding the concepts that we like and the modifications we are looking for. First, let me mention some of the design functions we like. - At the top of the homepage we really like the "region" or "language" tab so that the website can be viewed in both English and Arabic. - We like the homepage to have clear color variation so that the different sections of the homepage are distinct. Additionally, we like the bottom portion of the homepage to be in red. We feel that draws attention to our contact information. Again, we would like the colors to integrate black, gray-scale, red, etc. - Having a search tab at the top of the home page, or integrated into the main image, so that the site is easy to navigate. - We especially like the main image to have the scrolling tabs at the bottom so it is easy to browse the services offered (Consultancy, Solutions Architecture, Masters Systems Integration, Independent Design Review). - In regards to the services offered tab we really like the idea that a few people presented that have the outside of our logo with an icon in the middle of consultancy, solutions, etc., etc. Secondly, as mentioned in our brief we really enjoy the design of norvique site. Specially, we enjoy the strong iconic images they use, the way the tabs at the top scroll easily, and contact us page that generates an email. Lastly, I've included some photos of the concept we have been working on. What we are trying to demonstrate is how our company offers a range of services that are essentially linked together. We provide individual services that when combined present the full service package. We would like this concept to be integrated into the over concept of our website. Please feel free to ask for clarification of any of the above points or contact us if you have any additional questions. We appreciate all of your hard work and are very excited to see the updated designs. Best, Marta Vennick Quelbrant Senior Program Manager marta.vennick@quelbrant-example.com

Industry/Entity Type

Government

Font styles to use
Serif
Sans Serif

Requirements
Must have
• Must work on/adapt to various/mobile devices (responsive)
Must be simple and straightforward
Colors should be in line/matching with logo
2 language versions: English and Arabic (no Thai)
Services should be the first group/row of items after/below the main image
Note: the website will be hosted by hostpelican
Nice to have
• Submit feedback form
What's New section
The banner at the bottom of the site should not be too large; we would like a narrow one more
It would be nice if the header/top banner (with Home, About, etc. tabs) could stay in place as you scroll down (like Norvique and Chatterloop)
We will likely only use one image with a Company slogan on the Home page rather than a carousel of images to rotate through
Should not have
• This is the existing website: http://www.quelbrant-example.org
We do not like the animation, the way the banner icons/titles bounce
Not simple enough, we don't like the functionality or how pages load so slowly
We do not like the logo centered - it should be at the left
The banner and its tabs should not be towards the right, we would like them to be centered, to go all the way across and to be below the logo

```html
<!DOCTYPE html>
<html lang="en">
<head>
<meta charset="utf-8">
<title>Quelbrant – Systems and Technology Consultants</title>
<link href="https://fonts.googleapis.com/css2?family=Open+Sans:wght@400;600;700&display=swap" rel="stylesheet">
<style>
:root{
  --red:#d7262d;
  --dark:#2b2b2b;
  --footer:#3b3b3b;
  --footer-bar:#2e2e2e;
  --grey-band:#e9e9e9;
  --panel:#f3f3f3;
  --text:#555;
  --muted:#8a8a8a;
  --white:#fff;
}
*{box-sizing:border-box;margin:0;padding:0}
html,body{width:847px;height:1200px;overflow:hidden;background:var(--white)}
body{font-family:"Open Sans",Arial,sans-serif;color:var(--text);position:relative}
.site-header{position:absolute;top:0;left:0;width:847px;height:48px;background:var(--white);border-bottom:1px solid #e2e2e2}
.brand{position:absolute;left:26px;top:12px;display:flex;align-items:center;gap:6px}
.brand-mark{width:14px;height:14px;background:var(--red)}
.brand-name{font-weight:700;font-size:18px;color:var(--red);letter-spacing:.5px}
.main-nav{position:absolute;left:250px;top:17px;display:flex;gap:20px;font-size:9.5px;color:#444;text-transform:uppercase}
.main-nav span.caret::after{content:" ▾";font-size:7px}
.search{position:absolute;right:30px;top:13px;width:110px;height:20px;border:1px solid #ccc;background:#fafafa}
.search svg{position:absolute;right:5px;top:4px}
.hero{position:absolute;top:48px;left:0;width:847px;height:390px;background:radial-gradient(ellipse at 60% 45%,#c9d2da 0%,#7e8d9b 45%,#3f4b57 100%)}
.hero-tag{position:absolute;left:48px;top:140px}
.hero-title{display:inline-block;background:var(--dark);color:var(--white);font-size:15px;font-weight:700;padding:7px 12px;letter-spacing:.3px}
.hero-sub{background:rgba(255,255,255,.85);color:#333;font-size:9.5px;padding:6px 12px;width:262px;line-height:1.4}
.btn{display:inline-block;background:var(--red);color:var(--white);font-size:10px;font-weight:700;text-transform:uppercase;padding:7px 14px}
.hero .btn{margin-top:10px}
.hero-dots{position:absolute;bottom:14px;left:50%;transform:translateX(-50%);display:flex;gap:6px}
.hero-dots i{width:7px;height:7px;border-radius:50%;background:rgba(255,255,255,.6)}
.hero-dots i:first-child{background:var(--red)}
.vision{position:absolute;left:30px;top:458px;width:470px;height:222px;background:var(--panel);padding:18px 20px}
.vision h2{font-size:15px;color:#333;font-weight:600;margin-bottom:12px}
.vision p{font-size:8.5px;line-height:1.55;margin-bottom:8px;color:#666}
.news{position:absolute;left:520px;top:450px;width:300px}
.news h2{font-size:15px;color:#333;font-weight:600;padding-bottom:6px;border-bottom:1px solid #ddd;margin-bottom:10px}
.news-item{display:flex;gap:10px;margin-bottom:12px}
.news-thumb{width:58px;height:42px;background:linear-gradient(135deg,#9fb3c2,#5d6c78);flex:none}
.news-date{font-size:9px;font-weight:700;color:#333}
.news-title{font-size:12px;color:#222}
.news-text{font-size:8px;color:#777;line-height:1.4}
.news-more{font-size:8px;color:var(--red);text-align:right}
.services{position:absolute;top:695px;left:0;width:847px;height:240px;background:var(--grey-band)}
.service-list{position:absolute;left:72px;top:22px;display:flex;gap:22px}
.service-card{width:220px;height:195px;background:var(--white)}
.service-photo{height:95px}
.service-card h3{font-size:13px;font-weight:600;color:#333;text-align:center;text-transform:uppercase;margin:9px 0 5px}
.service-card p{font-size:8px;color:#777;line-height:1.45;padding:0 22px;text-align:center}
.service-card .btn{display:block;width:62px;margin:6px 22px 0 auto;font-size:8px;padding:4px 6px;text-transform:none;text-align:center}
.arrow{position:absolute;top:105px;width:22px;height:30px;background:#fff;display:flex;align-items:center;justify-content:center}
.arrow.prev{left:30px}.arrow.next{right:30px}
.site-footer{position:absolute;top:960px;left:0;width:847px;height:240px;background:var(--footer)}
.footer-cols{position:absolute;left:50px;top:20px;display:flex;gap:40px}
.footer-col h4{color:var(--red);font-size:9px;text-transform:uppercase;margin-bottom:6px}
.footer-col li{list-style:none;font-size:8px;color:#bbb;line-height:1.6}
.contact{position:absolute;left:320px;top:20px;color:#ddd;font-size:11px}
.contact div{display:flex;align-items:center;gap:8px;margin-bottom:8px}
.newsletter{position:absolute;left:590px;top:20px}
.newsletter h4{color:var(--red);font-size:9px;text-transform:uppercase;margin-bottom:8px}
.newsletter-form{display:flex}
.newsletter-form span{width:150px;height:22px;background:#fff;font-size:8px;color:#999;padding:6px 8px}
.newsletter-form .btn{font-size:8px;padding:6px 10px}
.footer-bar{position:absolute;bottom:0;left:0;width:847px;height:52px;background:var(--footer-bar)}
.copyright{position:absolute;left:50px;top:20px;font-size:8px;color:#999;text-transform:uppercase}
.social{position:absolute;right:50px;top:15px;display:flex;gap:6px}
.social i{width:20px;height:20px;border-radius:50%;background:#4a8fc0}
</style>
</head>
<body>
<header class="site-header">
  <div class="brand"><span class="brand-mark"></span><span class="brand-name">Quelbrant</span></div>
  <nav class="main-nav">
    <span>Home</span><span>Business Units</span><span class="caret">Services</span><span class="caret">About Us</span><span class="caret">Locations</span><span>Contact Us</span>
  </nav>
  <div class="search"><svg width="11" height="11" viewBox="0 0 11 11"><circle cx="4.5" cy="4.5" r="3.5" fill="none" stroke="#888" stroke-width="1.3"/><line x1="7" y1="7" x2="10" y2="10" stroke="#888" stroke-width="1.3"/></svg></div>
</header>

<section class="hero" role="img" aria-label="World map with glowing flight routes and an airliner">
  <div class="hero-tag">
    <div class="hero-title">WE ARE THE SYSTEM PROFESSIONALS</div>
    <div class="hero-sub">We deliver quality professional services and technical projects that support larger business goals.</div>
    <span class="btn">Know More</span>
  </div>
  <div class="hero-dots"><i></i><i></i><i></i></div>
</section>

<section class="vision">
  <h2>QUELBRANT - OUR VISION</h2>
  <p>Quelbrant specialises in delivering quality professional services and technical projects that support larger business goals. Systems and services are joined together to form one complete offer, shaped around the needs of every client we serve across each sector.</p>
  <p>Our teams recognise that the public and private sectors are growing, and that markets reward clear planning, careful integration and independent review. We bring these strengths together in one partner.</p>
  <p>Our ultimate goal is to provide quality technical and professional services on projects of any size and complexity from conception through to completion.</p>
</section>

<section class="news">
  <h2>NEWS &amp; EVENTS</h2>
  <div class="news-item">
    <div class="news-thumb" role="img" aria-label="Team meeting photo"></div>
    <div><div class="news-date">23/February/2014</div><div class="news-title">Emotional Intelligence</div><div class="news-text">Click here to see our latest article.</div><div class="news-more">Read more</div></div>
  </div>
  <div class="news-item">
    <div class="news-thumb" role="img" aria-label="Training session photo"></div>
    <div><div class="news-date">23/February/2014</div><div class="news-text">* 7 weekly training dates available in August<br>* Moderator boot camp dates available in June</div><div class="news-more">Read more</div></div>
  </div>
  <div class="news-item">
    <div class="news-thumb" role="img" aria-label="Workshop photo"></div>
    <div><div class="news-date">23/February/2014</div><div class="news-title">Emotional Intelligence</div><div class="news-text">Click here to see our latest article.</div><div class="news-more">Read more</div></div>
  </div>
</section>

<section class="services">
  <span class="arrow prev"><svg width="8" height="12"><polyline points="7,1 2,6 7,11" fill="none" stroke="#999" stroke-width="1.5"/></svg></span>
  <div class="service-list">
    <article class="service-card">
      <div class="service-photo" role="img" aria-label="Consultants at work" style="background:linear-gradient(135deg,#b8c2cc,#5b6874)"></div>
      <h3>Consulting</h3><p>Clear advice for planning, review and delivery of complex systems projects.</p><span class="btn">Read more</span>
    </article>
    <article class="service-card">
      <div class="service-photo" role="img" aria-label="Engineering blueprints and tools" style="background:linear-gradient(135deg,#7fa0c0,#2f4a66)"></div>
      <h3>Engineering</h3><p>Design and integration of systems for transport, government and business.</p><span class="btn">Read more</span>
    </article>
    <article class="service-card">
      <div class="service-photo" role="img" aria-label="Construction site with cranes" style="background:linear-gradient(135deg,#f0c46a,#8a6a3a)"></div>
      <h3>Construction</h3><p>Site delivery and supervision from early works through to handover.</p><span class="btn">Read more</span>
    </article>
  </div>
  <span class="arrow next"><svg width="8" height="12"><polyline points="1,1 6,6 1,11" fill="none" stroke="#999" stroke-width="1.5"/></svg></span>
</section>

<footer class="site-footer">
  <div class="footer-cols">
    <div class="footer-col"><h4>Quick Links</h4><ul><li>About Us</li><li>Services</li><li>Careers</li><li>Locations</li><li>Contact</li></ul></div>
    <div class="footer-col"><h4>Services</h4><ul><li>Consulting</li><li>Engineering</li><li>Construction</li><li>Review</li></ul></div>
  </div>
  <div class="contact">
    <div><svg width="12" height="12" viewBox="0 0 12 12"><path d="M2 1h3l1 3-2 1a7 7 0 0 0 3 3l1-2 3 1v3c-6 0-11-5-11-11z" fill="#ccc"/></svg>+(000) 555-0142</div>
    <div><svg width="12" height="10" viewBox="0 0 12 10"><rect x="0.5" y="0.5" width="11" height="9" fill="none" stroke="#ccc"/><polyline points="0.5,0.5 6,5 11.5,0.5" fill="none" stroke="#ccc"/></svg>info@quelbrant-example.org</div>
  </div>
  <div class="newsletter">
    <h4>Newsletter Signup</h4>
    <div class="newsletter-form"><span>enter your email address</span><span class="btn">Sign Up</span></div>
  </div>
  <div class="footer-bar">
    <div class="copyright">© 2014 Quelbrant. All rights reserved</div>
    <div class="social"><i></i><i></i><i></i><i></i></div>
  </div>
</footer>
</body>
</html>
```